App Design Project

Hello,
I'm looking for a great designer for my iOS Applications, we have a lot of works and we're short in designers :(
I want to revamp my thermometer iOS app. You will find attached the images I want to replace. I need something with the same element (temp, condition, weather icon) but with a different look!
Same, new icon, you have carte blanche to this one.
I want a design that stands out from the hundreds of weather application that almost all the same design. I am looking for something that does say "wow, it rocks."
Please do not Provide classic design that we can see everywhere ... I'm looking for something with a real artistic choice, contrast, colours, etc.
As a marketing screenshot, I want something classic, you'll find an example attached, feel free to innovate.
To sum-up :
- One new view for my App
- One new icon
- One marketing screenshot
Marketing

```html
<!DOCTYPE html>
<html lang="en">
<head>
<meta charset="utf-8">
<title>Thermometer for Skyphone</title>
<link href="https://fonts.googleapis.com/css2?family=Antonio:wght@200;400&family=Roboto+Condensed:wght@400;700&display=swap" rel="stylesheet">
<style>
  :root{
    --sky-blue:#3d9ee3;
    --sky-blue-dark:#1f7fc8;
    --strip-blue:#2f9ee6;
    --ring-blue:#2f9ee6;
    --night:#23272d;
    --slate:#3a3c40;
    --slate-light:#55585d;
    --white:#ffffff;
    --tag:#262626;
    --toggle-grey:rgba(255,255,255,.75);
  }
  *{box-sizing:border-box;margin:0;padding:0}
  html,body{width:1200px;height:1000px;overflow:hidden;background:#fff}
  .canvas{position:relative;width:1200px;height:1000px;overflow:hidden}

  .panel-left-top{position:absolute;left:0;top:0;width:570px;height:565px;background:linear-gradient(180deg,#5cb3ee,var(--sky-blue-dark))}
  .panel-left-bottom{position:absolute;left:0;top:565px;width:570px;height:435px;background:linear-gradient(180deg,var(--night) 0,var(--night) 170px,var(--sky-blue) 170px,#6ab9ee 100%)}
  .panel-right{position:absolute;left:635px;top:0;width:565px;height:1000px;background:radial-gradient(circle at 60% 40%,var(--slate-light),var(--slate))}

  .promo{position:absolute;font-family:'Roboto Condensed',sans-serif;color:var(--white);text-align:center;line-height:1.05}
  .promo-title{font-weight:700;font-size:36px;letter-spacing:.5px}
  .promo-for{font-style:italic;font-size:30px;font-weight:400}
  .promo-platform{font-size:30px;font-weight:400}
  .app-icon{position:absolute;border-radius:22%;background:linear-gradient(180deg,#6cc6f5,var(--sky-blue-dark));box-shadow:0 4px 10px rgba(0,0,0,.35)}

  /* weather screen */
  .screen{position:absolute;width:16em;height:28em;overflow:hidden;color:var(--white);font-family:'Antonio',sans-serif;display:flex;flex-direction:column}
  .photo{position:absolute;inset:0}
  .clear .photo{background:linear-gradient(200deg,#dbe9f6 0%,#6f9fdc 45%,#2d62c0 100%)}
  .hail .photo{background:linear-gradient(180deg,#c8ced3,#8b949c 60%,#5d656c)}
  .wind .photo{background:linear-gradient(180deg,#aab3b8,#c9b07a 50%,#6e5b3a)}
  .snow .photo{background:linear-gradient(180deg,#c7d1da,#e8edf1 50%,#8d9aa6)}
  .rain .photo{background:linear-gradient(180deg,#6b746e,#3f4641 50%,#2a2e2b)}
  .sky{position:relative;flex:1;display:flex;flex-direction:column;align-items:center}
  .tag{position:absolute;top:1.2em;right:0;background:var(--tag);font:700 .55em 'Roboto Condensed',sans-serif;letter-spacing:.12em;padding:.45em .9em}
  .glyph{width:6.4em;height:6.4em;margin-top:3.4em}
  .cond{font-size:2.3em;font-weight:200;line-height:1.15;letter-spacing:.04em}
  .rule{width:100%;height:1px;background:rgba(255,255,255,.4);margin:.4em 0 .2em}
  .temp{display:flex;align-items:center;gap:.3em;font-size:3.1em;font-weight:200;line-height:1.1}
  .temp svg{width:.35em;height:.7em}
  .unit-toggle{position:absolute;right:.8em;bottom:.9em;display:flex;align-items:flex-end;gap:.15em}
  .unit-box{display:block;width:.9em;height:.9em;background:var(--toggle-grey)}
  .unit-label{font:700 .55em 'Roboto Condensed',sans-serif;color:var(--strip-blue);line-height:1}
  .stats{position:relative;height:4.4em;background:rgba(18,18,18,.72);display:flex;align-items:center}
  .stat{display:flex;align-items:center;gap:.5em;padding:0 .7em;height:100%}
  .stat + .stat{border-left:1px solid rgba(255,255,255,.15)}
  .ring{width:3.2em;height:3.2em;position:relative;display:flex;align-items:center;justify-content:center;font:400 .95em 'Roboto Condensed',sans-serif}
  .ring svg{position:absolute;inset:0;width:100%;height:100%}
  .wind-speed{font:400 .9em 'Roboto Condensed',sans-serif;letter-spacing:.05em;white-space:nowrap}
  .small-icon{width:1.3em;height:1.3em;flex:none}
  .forecast{position:relative;height:3.6em;background:var(--strip-blue);display:grid;grid-template-columns:repeat(4,1fr);font-family:'Roboto Condensed',sans-serif}
  .day{display:flex;flex-direction:column;align-items:center;padding-top:.35em}
  .day-name{font-size:.55em;font-weight:700;letter-spacing:.05em}
  .day-data{display:flex;align-items:center;gap:.25em;margin-top:.2em}
  .day-data svg{width:1.1em;height:1.1em}
  .day-temps{font-size:.48em;line-height:1.2}
  .landscape{transform:rotate(90deg);transform-origin:center}
</style>
</head>
<body>
<div class="canvas">

  <section class="panel-left-top">
    <!-- clear -->
    <div class="screen clear" style="font-size:10px;left:40px;top:95px">
      <div class="photo" role="img" aria-label="Photo of a bright blue sky"></div>
      <div class="sky">
        <span class="tag">LONDON, UK</span>
        <svg class="glyph" viewBox="0 0 48 48" fill="none" stroke="#fff" stroke-width="2.6" stroke-linecap="round"><circle cx="24" cy="24" r="8"/><path d="M24 6v6M24 36v6M6 24h6M36 24h6M11 11l4 4M33 33l4 4M37 11l-4 4M15 33l-4 4"/></svg>
        <div class="cond">Clear</div>
        <div class="rule"></div>
        <div class="temp"><svg viewBox="0 0 10 20"><rect x="3" y="1" width="4" height="13" rx="2" fill="#fff"/><circle cx="5" cy="16" r="3.5" fill="#fff"/></svg>24°C</div>
      </div>
      <div class="stats">
        <div class="stat"><svg class="small-icon" viewBox="0 0 24 24" fill="none" stroke="#fff" stroke-width="2" stroke-linecap="round"><path d="M3 9h12a3 3 0 1 0-3-3M3 15h15a3 3 0 1 1-3 3"/></svg>
          <div class="ring"><svg viewBox="0 0 40 40"><circle cx="20" cy="20" r="17" stroke="#444" stroke-width="4" fill="none"/><circle cx="20" cy="20" r="17" stroke="var(--ring-blue)" stroke-width="4" fill="none" stroke-dasharray="70 107" transform="rotate(90 20 20)"/></svg>30 %</div></div>
        <div class="stat"><span class="wind-speed">N 39</span></div>
      </div>
      <div class="forecast">
        <div class="day"><span class="day-name">MON</span><div class="day-data"><svg viewBox="0 0 24 24" fill="none" stroke="#fff" stroke-width="2"><path d="M7 18h10a4 4 0 0 0 0-8 6 6 0 0 0-11 2 3 3 0 0 0 1 6z"/></svg><span class="day-temps">25°<br>19°</span></div></div>
        <div class="day"><span class="day-name">TUES</span><div class="day-data"><svg viewBox="0 0 24 24" fill="none" stroke="#fff" stroke-width="2"><path d="M7 18h10a4 4 0 0 0 0-8 6 6 0 0 0-11 2 3 3 0 0 0 1 6z"/></svg><span class="day-temps">18°<br>14°</span></div></div>
        <div class="day"><span class="day-name">WEDS</span><div class="day-data"><svg viewBox="0 0 24 24" fill="none" stroke="#fff" stroke-width="2"><path d="M7 18h10a4 4 0 0 0 0-8 6 6 0 0 0-11 2 3 3 0 0 0 1 6z"/></svg><span class="day-temps">12°<br>6°</span></div></div>
        <div class="day"><span class="day-name">THURS</span><div class="day-data"><svg viewBox="0 0 24 24" fill="none" stroke="#fff" stroke-width="2"><path d="M7 18h10a4 4 0 0 0 0-8 6 6 0 0 0-11 2 3 3 0 0 0 1 6z"/></svg><span class="day-temps">25°<br>19°</span></div></div>
      </div>
    </div>

    <!-- hail -->
    <div class="screen hail" style="font-size:10px;left:205px;top:95px">
      <div class="photo" role="img" aria-label="Photo of hailstones"></div>
      <div class="sky">
        <span class="tag">LONDON, UK</span>
        <svg class="glyph" viewBox="0 0 48 48" fill="none" stroke="#fff" stroke-width="2.6" stroke-linecap="round"><path d="M13 32a8 8 0 0 1 1-16 11 11 0 0 1 21 3 7 7 0 0 1-1 13"/><path d="M20 26v10M24 24v14M28 26v10"/></svg>
        <div class="cond">Hail</div>
        <div class="rule"></div>
        <div class="temp"><svg viewBox="0 0 10 20"><rect x="3" y="1" width="4" height="13" rx="2" fill="#fff"/><circle cx="5" cy="16" r="3.5" fill="#fff"/></svg>-10°C</div>
      </div>
      <div class="stats">
        <div class="stat"><svg class="small-icon" viewBox="0 0 24 24" fill="none" stroke="#fff" stroke-width="2" stroke-linecap="round"><path d="M3 9h12a3 3 0 1 0-3-3M3 15h15a3 3 0 1 1-3 3"/></svg>
          <div class="ring"><svg viewBox="0 0 40 40"><circle cx="20" cy="20" r="17" stroke="#444" stroke-width="4" fill="none"/><circle cx="20" cy="20" r="17" stroke="var(--ring-blue)" stroke-width="4" fill="none" stroke-dasharray="70 107" transform="rotate(90 20 20)"/></svg>30 %</div></div>
        <div class="stat"><span class="wind-speed">N 39</span></div>
      </div>
      <div class="forecast">
        <div class="day"><span class="day-name">MON</span><div class="day-data"><svg viewBox="0 0 24 24" fill="none" stroke="#fff" stroke-width="2"><path d="M7 18h10a4 4 0 0 0 0-8 6 6 0 0 0-11 2 3 3 0 0 0 1 6z"/></svg><span class="day-temps">25°<br>19°</span></div></div>
        <div class="day"><span class="day-name">TUES</span><div class="day-data"><svg viewBox="0 0 24 24" fill="none" stroke="#fff" stroke-width="2"><path d="M7 18h10a4 4 0 0 0 0-8 6 6 0 0 0-11 2 3 3 0 0 0 1 6z"/></svg><span class="day-temps">18°<br>14°</span></div></div>
        <div class="day"><span class="day-name">WEDS</span><div class="day-data"><svg viewBox="0 0 24 24" fill="none" stroke="#fff" stroke-width="2"><path d="M7 18h10a4 4 0 0 0 0-8 6 6 0 0 0-11 2 3 3 0 0 0 1 6z"/></svg><span class="day-temps">12°<br>6°</span></div></div>
        <div class="day"><span class="day-name">THURS</span><div class="day-data"><svg viewBox="0 0 24 24" fill="none" stroke="#fff" stroke-width="2"><path d="M7 18h10a4 4 0 0 0 0-8 6 6 0 0 0-11 2 3 3 0 0 0 1 6z"/></svg><span class="day-temps">25°<br>19°</span></div></div>
      </div>
    </div>

    <!-- wind -->
    <div class="screen wind" style="font-size:10px;left:370px;top:95px">
      <div class="photo" role="img" aria-label="Photo of tall grass in the wind"></div>
      <div class="sky">
        <span class="tag">LONDON, UK</span>
        <svg class="glyph" viewBox="0 0 48 48" fill="none" stroke="#fff" stroke-width="2.6" stroke-linecap="round"><path d="M12 30a8 8 0 0 1 1-16 11 11 0 0 1 21 3"/><path d="M16 26h20a4 4 0 1 0-4-4M16 32h24a4 4 0 1 1-4 4"/></svg>
        <div class="cond">Wind</div>
        <div class="rule"></div>
        <div class="temp"><svg viewBox="0 0 10 20"><rect x="3" y="1" width="4" height="13" rx="2" fill="#fff"/><circle cx="5" cy="16" r="3.5" fill="#fff"/></svg>25°C</div>
        <span class="unit-toggle"><i class="unit-box"></i><b class="unit-label">°C</b></span>
      </div>
      <div class="stats">
        <div class="stat"><svg class="small-icon" viewBox="0 0 24 24" fill="none" stroke="#fff" stroke-width="2" stroke-linecap="round"><path d="M3 9h12a3 3 0 1 0-3-3M3 15h15a3 3 0 1 1-3 3"/></svg>
          <div class="ring"><svg viewBox="0 0 40 40"><circle cx="20" cy="20" r="17" stroke="#444" stroke-width="4" fill="none"/><circle cx="20" cy="20" r="17" stroke="var(--ring-blue)" stroke-width="4" fill="none" stroke-dasharray="70 107" transform="rotate(90 20 20)"/></svg>30 %</div></div>
        <div class="stat"><span class="wind-speed">N 39 km/h</span></div>
      </div>
      <div class="forecast">
        <div class="day"><span class="day-name">MON</span><div class="day-data"><svg viewBox="0 0 24 24" fill="none" stroke="#fff" stroke-width="2"><path d="M7 18h10a4 4 0 0 0 0-8 6 6 0 0 0-11 2 3 3 0 0 0 1 6z"/></svg><span class="day-temps">25°<br>19°</span></div></div>
        <div class="day"><span class="day-name">TUES</span><div class="day-data"><svg viewBox="0 0 24 24" fill="none" stroke="#fff" stroke-width="2"><path d="M7 18h10a4 4 0 0 0 0-8 6 6 0 0 0-11 2 3 3 0 0 0 1 6z"/></svg><span class="day-temps">18°<br>14°</span></div></div>
        <div class="day"><span class="day-name">WEDS</span><div class="day-data"><svg viewBox="0 0 24 24" fill="none" stroke="#fff" stroke-width="2"><path d="M7 18h10a4 4 0 0 0 0-8 6 6 0 0 0-11 2 3 3 0 0 0 1 6z"/></svg><span class="day-temps">12°<br>6°</span></div></div>
        <div class="day"><span class="day-name">THURS</span><div class="day-data"><svg viewBox="0 0 24 24" fill="none" stroke="#fff" stroke-width="2"><path d="M7 18h10a4 4 0 0 0 0-8 6 6 0 0 0-11 2 3 3 0 0 0 1 6z"/></svg><span class="day-temps">25°<br>19°</span></div></div>
      </div>
    </div>
  </section>

  <section class="panel-left-bottom">
    <div class="promo" style="left:20px;top:38px;width:235px">
      <div class="promo-title">THERMOMETER</div>
      <div class="promo-for">for</div>
      <div class="promo-platform">Skyphone</div>
    </div>
    <div class="app-icon" style="left:272px;top:30px;width:78px;height:78px"></div>

    <!-- rain, landscape -->
    <div class="screen rain landscape" style="font-size:14px;left:173px;top:95px">
      <div class="photo" role="img" aria-label="Photo of raindrops on a window"></div>
      <div class="sky">
        <span class="tag">LONDON, UK</span>
        <svg class="glyph" viewBox="0 0 48 48" fill="none" stroke="#fff" stroke-width="3.4" stroke-linecap="round"><path d="M12 30a8 8 0 0 1 1-16 11 11 0 0 1 21 3 7 7 0 0 1 1 13"/><path d="M19 24v12M25 24v16M31 24v12"/></svg>
        <div class="cond">Rain</div>
        <div class="rule"></div>
        <div class="temp"><svg viewBox="0 0 10 20"><rect x="3" y="1" width="4" height="13" rx="2" fill="#fff"/><circle cx="5" cy="16" r="3.5" fill="#fff"/></svg>9°C</div>
        <span class="unit-toggle"><i class="unit-box"></i><b class="unit-label">°C</b></span>
      </div>
      <div class="stats">
        <div class="stat"><svg class="small-icon" viewBox="0 0 24 24" fill="none" stroke="#fff" stroke-width="2" stroke-linecap="round"><path d="M3 9h12a3 3 0 1 0-3-3M3 15h15a3 3 0 1 1-3 3"/></svg>
          <div class="ring"><svg viewBox="0 0 40 40"><circle cx="20" cy="20" r="17" stroke="#444" stroke-width="4" fill="none"/><circle cx="20" cy="20" r="17" stroke="var(--ring-blue)" stroke-width="4" fill="none" stroke-dasharray="70 107" transform="rotate(90 20 20)"/></svg>30 %</div></div>
        <div class="stat"><svg class="small-icon" viewBox="0 0 24 24"><circle cx="12" cy="12" r="9" fill="#fff"/><circle cx="12" cy="12" r="3.5" fill="#222"/></svg><span class="wind-speed">N 39 km/h</span></div>
      </div>
      <div class="forecast">
        <div class="day"><span class="day-name">MON</span><div class="day-data"><svg viewBox="0 0 24 24" fill="none" stroke="#fff" stroke-width="2"><path d="M7 18h10a4 4 0 0 0 0-8 6 6 0 0 0-11 2 3 3 0 0 0 1 6z"/></svg><span class="day-temps">25°<br>19°</span></div></div>
        <div class="day"><span class="day-name">TUES</span><div class="day-data"><svg viewBox="0 0 24 24" fill="none" stroke="#fff" stroke-width="2"><path d="M7 18h10a4 4 0 0 0 0-8 6 6 0 0 0-11 2 3 3 0 0 0 1 6z"/></svg><span class="day-temps">18°<br>14°</span></div></div>
        <div class="day"><span class="day-name">WEDS</span><div class="day-data"><svg viewBox="0 0 24 24" fill="none" stroke="#fff" stroke-width="2"><path d="M7 18h10a4 4 0 0 0 0-8 6 6 0 0 0-11 2 3 3 0 0 0 1 6z"/></svg><span class="day-temps">12°<br>6°</span></div></div>
        <div class="day"><span class="day-name">THURS</span><div class="day-data"><svg viewBox="0 0 24 24" fill="none" stroke="#fff" stroke-width="2"><path d="M7 18h10a4 4 0 0 0 0-8 6 6 0 0 0-11 2 3 3 0 0 0 1 6z"/></svg><span class="day-temps">25°<br>19°</span></div></div>
      </div>
    </div>
  </section>

  <section class="panel-right">
    <!-- snow -->
    <div class="screen snow" style="font-size:13.75px;left:33px;top:115px">
      <div class="photo" role="img" aria-label="Photo of snowy mountains"></div>
      <div class="sky">
        <span class="tag">LONDON, UK</span>
        <svg class="glyph" viewBox="0 0 48 48" fill="none" stroke="#fff" stroke-width="3.4" stroke-linecap="round"><path d="M12 32a8 8 0 0 1 1-16 11 11 0 0 1 21 3 7 7 0 0 1 1 13"/><path d="M24 27v10M19.7 29.5l8.6 5M28.3 29.5l-8.6 5"/></svg>
        <div class="cond">Snow</div>
        <div class="rule"></div>
        <div class="temp"><svg viewBox="0 0 10 20"><rect x="3" y="1" width="4" height="13" rx="2" fill="#fff"/><circle cx="5" cy="16" r="3.5" fill="#fff"/></svg>-5°C</div>
        <span class="unit-toggle"><i class="unit-box"></i><b class="unit-label">°C</b></span>
      </div>
      <div class="stats">
        <div class="stat"><svg class="small-icon" viewBox="0 0 24 24" fill="none" stroke="#fff" stroke-width="2" stroke-linecap="round"><path d="M3 9h12a3 3 0 1 0-3-3M3 15h15a3 3 0 1 1-3 3"/></svg>
          <div class="ring"><svg viewBox="0 0 40 40"><circle cx="20" cy="20" r="17" stroke="#444" stroke-width="4" fill="none"/><circle cx="20" cy="20" r="17" stroke="var(--ring-blue)" stroke-width="4" fill="none" stroke-dasharray="70 107" transform="rotate(90 20 20)"/></svg>30 %</div></div>
        <div class="stat"><svg class="small-icon" viewBox="0 0 24 24"><circle cx="12" cy="12" r="9" fill="#fff"/><circle cx="12" cy="12" r="3.5" fill="#222"/></svg><span class="wind-speed">N 39 km/h</span></div>
      </div>
      <div class="forecast">
        <div class="day"><span class="day-name">MON</span><div class="day-data"><svg viewBox="0 0 24 24" fill="none" stroke="#fff" stroke-width="2"><path d="M7 18h10a4 4 0 0 0 0-8 6 6 0 0 0-11 2 3 3 0 0 0 1 6z"/></svg><span class="day-temps">25°<br>19°</span></div></div>
        <div class="day"><span class="day-name">TUES</span><div class="day-data"><svg viewBox="0 0 24 24" fill="none" stroke="#fff" stroke-width="2"><path d="M7 18h10a4 4 0 0 0 0-8 6 6 0 0 0-11 2 3 3 0 0 0 1 6z"/></svg><span class="day-temps">18°<br>14°</span></div></div>
        <div class="day"><span class="day-name">WEDS</span><div class="day-data"><svg viewBox="0 0 24 24" fill="none" stroke="#fff" stroke-width="2"><path d="M7 18h10a4 4 0 0 0 0-8 6 6 0 0 0-11 2 3 3 0 0 0 1 6z"/></svg><span class="day-temps">12°<br>6°</span></div></div>
        <div class="day"><span class="day-name">THURS</span><div class="day-data"><svg viewBox="0 0 24 24" fill="none" stroke="#fff" stroke-width="2"><path d="M7 18h10a4 4 0 0 0 0-8 6 6 0 0 0-11 2 3 3 0 0 0 1 6z"/></svg><span class="day-temps">25°<br>19°</span></div></div>
      </div>
    </div>

    <div class="promo" style="left:280px;top:110px;width:270px">
      <div class="promo-title">THERMOMETER</div>
      <div class="promo-for">for</div>
      <div class="promo-platform">Skyphone</div>
    </div>
    <div class="app-icon" style="left:353px;top:275px;width:118px;height:118px"></div>

    <!-- rain, landscape -->
    <div class="screen rain landscape" style="font-size:14px;left:200px;top:525px">
      <div class="photo" role="img" aria-label="Photo of raindrops on a window"></div>
      <div class="sky">
        <span class="tag">LONDON, UK</span>
        <svg class="glyph" viewBox="0 0 48 48" fill="none" stroke="#fff" stroke-width="3.4" stroke-linecap="round"><path d="M12 30a8 8 0 0 1 1-16 11 11 0 0 1 21 3 7 7 0 0 1 1 13"/><path d="M19 24v12M25 24v16M31 24v12"/></svg>
        <div class="cond">Rain</div>
        <div class="rule"></div>
        <div class="temp"><svg viewBox="0 0 10 20"><rect x="3" y="1" width="4" height="13" rx="2" fill="#fff"/><circle cx="5" cy="16" r="3.5" fill="#fff"/></svg>9°C</div>
        <span class="unit-toggle"><i class="unit-box"></i><b class="unit-label">°C</b></span>
      </div>
      <div class="stats">
        <div class="stat"><svg class="small-icon" viewBox="0 0 24 24" fill="none" stroke="#fff" stroke-width="2" stroke-linecap="round"><path d="M3 9h12a3 3 0 1 0-3-3M3 15h15a3 3 0 1 1-3 3"/></svg>
          <div class="ring"><svg viewBox="0 0 40 40"><circle cx="20" cy="20" r="17" stroke="#444" stroke-width="4" fill="none"/><circle cx="20" cy="20" r="17" stroke="var(--ring-blue)" stroke-width="4" fill="none" stroke-dasharray="70 107" transform="rotate(90 20 20)"/></svg>30 %</div></div>
        <div class="stat"><svg class="small-icon" viewBox="0 0 24 24"><circle cx="12" cy="12" r="9" fill="#fff"/><circle cx="12" cy="12" r="3.5" fill="#222"/></svg><span class="wind-speed">N 39 km/h</span></div>
      </div>
      <div class="forecast">
        <div class="day"><span class="day-name">MON</span><div class="day-data"><svg viewBox="0 0 24 24" fill="none" stroke="#fff" stroke-width="2"><path d="M7 18h10a4 4 0 0 0 0-8 6 6 0 0 0-11 2 3 3 0 0 0 1 6z"/></svg><span class="day-temps">25°<br>19°</span></div></div>
        <div class="day"><span class="day-name">TUES</span><div class="day-data"><svg viewBox="0 0 24 24" fill="none" stroke="#fff" stroke-width="2"><path d="M7 18h10a4 4 0 0 0 0-8 6 6 0 0 0-11 2 3 3 0 0 0 1 6z"/></svg><span class="day-temps">18°<br>14°</span></div></div>
        <div class="day"><span class="day-name">WEDS</span><div class="day-data"><svg viewBox="0 0 24 24" fill="none" stroke="#fff" stroke-width="2"><path d="M7 18h10a4 4 0 0 0 0-8 6 6 0 0 0-11 2 3 3 0 0 0 1 6z"/></svg><span class="day-temps">12°<br>6°</span></div></div>
        <div class="day"><span class="day-name">THURS</span><div class="day-data"><svg viewBox="0 0 24 24" fill="none" stroke="#fff" stroke-width="2"><path d="M7 18h10a4 4 0 0 0 0-8 6 6 0 0 0-11 2 3 3 0 0 0 1 6z"/></svg><span class="day-temps">25°<br>19°</span></div></div>
      </div>
    </div>
  </section>

</div>
</body>
</html>
```